Wine Bottle Label for Tall Fern Wines

We are a small, newly established winery in need of an original, bold and outstanding bottle label design for our Tall Fern wine.

Our vineyard and winery are located on a 200 acre farm in a remote part of southern Oregon. The name "Tall Fern" was inspired by the large, overgrown size of all of the foliage here, including our grapevines. Things grow large and vigorous in Oregon! And everything is very lush and green. It is almost surreal or other-worldly, like the landscapes seen in the Keeper of The Stones movies, or the land of Quill. It is a place that makes you say "wow" with its epic, large scale, natural beauty.

The name "Tall Fern" also captures the essence of our wine. It is big in flavor, quality and color. Our first release is a Pinot Noir (red). Pinot Noir wines often are subtle in flavor and thin in their color. Our label should convey that our Pinot Noir is a much more robust, darker, heavier, meatier, more flavorful wine that is a lot more fun than an "ordinary" wine. At the same time, this wine is not cheap, and so nothing in the label should convey "bargain," "low price," or "cheapness." This is a fine wine with a sense of adventure. Be sure to convey "quality" with your design along with "big," "adventure" and "fun".

The label should appeal to a younger demographic, both male and female, between the ages of 21 and 35. It should be non-traditional and adventurous and suggest a pushing of boundaries and a breaking of rules. This Pinot Noir does not conform to the normal "limitations" of the variety, therefore the label should not conform. It should have an "organic" or "natural" or "agricultural" vibe, as opposed to something mechanical or technical. It should, however, be contemporary. Do not confuse "natural" or "organic" with being nostalgic or old school. Think "agri-hipsters."

The label should be designed to fit on a Burgundy-style wine bottle (photo attached for reference). (Note: All Pinot Noir and Chardonnay is bottled in Burgundy bottles, If you are not sure about the bottle shape you can go to a local store and compare the various bottles. Locate a bottle of Pinot Noir or Chardonnay or anything identified as a "Burgundy Wine," and it should be the correct bottle. The tall, skinny bottles used for Cabernet Sauvignon are NOT correct)). Please see the "Must Have" notes for more on the bottle.

In summary, the final project should be a wine bottle label design that conveys bigness, vastness, adventurous, non-traditional, high quality wine. A good tagline to keep in mind is "Living Large."

Target Market(s)

Young, hip, non-conformist wine drinkers aged 21-35 with a sense of adventure and an appreciation of quality.

Industry/Entity Type

School

Requirements
Must have
• *Must contain the words:

Tall Fern (the brand)
2013 Pinot Noir (the vintage year and variety)

*The label must be designed to fit a Burgundy-style wine bottle. A photo is attached for reference.

*Additionally, the label needs to fit on the lower, widest part of the bottle. The label will be printed on sticky paper and rolled onto the bottle with a machine. The machine cannot apply labels to the neck of the bottle. The maximum size of a label that will fit this space is 5.5 inches wide by 4.5 inches tall. You DO NOT have to fill ALL of this space or confine the label shape to a rectangle, but the label cannot exceed this size or it won't stick to the bottle properly. It will really help if you can put your hands on an actual bottle to see the logistics of applying the label. But if that is not possible, just do your best with the instructions you have. I am confident the winning design could be adjusted to fit the bottle, if necessary
Nice to have
• *Wine grape leaf or leaves.

*A concept I have been playing with is sunlight shining through leaves like light through a Marlowe lamp or a stained glass window. This is NOT a requirement for this label. However, if the concept inspires and idea, I would be most happy to see it.
Should not have
• IF a leaf or leaves are included in the design (not a requirement) they MUST be wine grapevine leafs and preferably leaves of the Pinot Noir vine. Do not use generic leaves or identifiable leaves such as oak leaves, maple leaves, or anything that looks like the Canadian flag or the Halden Ridge Ravens hockey logo. Reference the attached photos of wine grape leaves to see the correct leaf type. I am happy to email more photos upon request. These photos may be used in whole or in part in your design, however, a leaf from a photo is NOT a requirement, nor is the image of a leaf or leaves.

This label should NOT be designed for Bordeaux-style wine bottles (the tall, skinny ones).

```html
<!DOCTYPE html>
<html lang="en">
<head>
<meta charset="utf-8">
<title>Tall Fern Wines – Pinot Noir Label</title>
<link rel="stylesheet" href="https://fonts.googleapis.com/css2?family=Griffy&family=Risque&display=swap">
<style>
  :root {
    --label-yellow: #fde64f;
    --leaf-red: #c8321f;
    --leaf-orange: #d9611e;
    --leaf-deep: #a8261a;
    --ink-black: #141414;
    --title-green: #274a2b;
    --halo: #fff6c8;
  }
  html, body {
    margin: 0;
    padding: 0;
    overflow: hidden;
    background: var(--label-yellow);
  }
  .label {
    position: relative;
    width: 1200px;
    height: 624px;
    overflow: hidden;
    background: var(--label-yellow);
    font-family: "Griffy", "Risque", cursive;
  }
  .label__art {
    position: absolute;
    inset: 0;
    width: 1200px;
    height: 624px;
  }
  .vintage-badge {
    position: absolute;
    left: 531px;
    top: 59px;
    width: 138px;
    height: 138px;
  }
  .vintage-badge__year {
    position: absolute;
    inset: 0;
    display: flex;
    align-items: center;
    justify-content: center;
    margin: 0;
    font-family: "Risque", cursive;
    font-size: 34px;
    color: var(--ink-black);
  }
  .brand-name {
    position: absolute;
    left: 290px;
    top: 228px;
    width: 620px;
    margin: 0;
    text-align: center;
    font-size: 138px;
    font-weight: 400;
    line-height: 1;
    color: var(--title-green);
    letter-spacing: 2px;
  }
  .variety {
    position: absolute;
    left: 0;
    width: 1200px;
    top: 492px;
    margin: 0;
    text-align: center;
    font-size: 46px;
    font-weight: 400;
    color: var(--ink-black);
  }
  .spec {
    position: absolute;
    top: 528px;
    margin: 0;
    font-size: 30px;
    color: var(--ink-black);
  }
  .spec--volume { left: 84px; }
  .spec--abv { right: 90px; }
</style>
</head>
<body>
  <main class="label">
    <svg class="label__art" viewBox="0 0 1200 624" xmlns="http://www.w3.org/2000/svg">
      <defs>
        <linearGradient id="leafTone" x1="0" y1="0" x2="1" y2="1">
          <stop offset="0" stop-color="#c95a22"/>
          <stop offset="0.45" stop-color="#c8321f"/>
          <stop offset="1" stop-color="#b8281b"/>
        </linearGradient>
        <filter id="haloBlur" x="-20%" y="-40%" width="140%" height="180%">
          <feGaussianBlur stdDeviation="18"/>
        </filter>
      </defs>
      <path class="grape-leaf" role="img" aria-label="Close-up of a red and orange autumn grapevine leaf with visible veins"
            fill="url(#leafTone)"
            d="M0 0 H1045 L1025 73 L935 146 L813 187 L691 236 L620 300 L520 400 L460 480 L439 504 L431 533 L366 537 L244 520 L114 504 L73 480 L0 472 Z"/>
      <rect class="title-halo" x="300" y="250" width="600" height="160" rx="80"
            fill="var(--halo)" opacity="0.75" filter="url(#haloBlur)"/>
    </svg>

    <div class="vintage-badge">
      <svg viewBox="0 0 138 138" width="138" height="138" aria-hidden="true">
        <circle cx="69" cy="69" r="69" fill="var(--ink-black)"/>
        <circle cx="69" cy="69" r="56" fill="var(--label-yellow)"/>
      </svg>
      <p class="vintage-badge__year">2013</p>
    </div>

    <h1 class="brand-name">Tall Fern</h1>
    <p class="variety">Pinot Noir</p>
    <p class="spec spec--volume">..CL</p>
    <p class="spec spec--abv">..%Vol</p>
  </main>
</body>
</html>
```